Tire trade

Hello, I would like to make A5 flyers for my garage, with the 'marvek tires' logo.
Registration: Sale and fitting of tires of all brands (also ordered by you) Guarding of your tires

Target Market(s)

All motorists in my area

Industry/Entity Type

Vente de pneus

Font styles to use
Serif

Colors
EE7325
F08F49
F5BC92
FAE3D3
FDF4ED

Requirements
Must have
• My logo, the place (Val-d'Aubrine)
Nice to have
• Simple and eye-catching
Should not have
• pink

```html
<!DOCTYPE html>
<html lang="en">
<head>
<meta charset="utf-8">
<title>Marvek Tires – A5 Flyer</title>
<link rel="stylesheet" href="https://fonts.googleapis.com/css2?family=Montserrat:ital,wght@0,800;0,900;1,800;1,900&display=swap">
<style>
  :root {
    --stage: #111111;
    --panel-black: #000000;
    --red-deep: #6e0800;
    --red-main: #d01a00;
    --red-bright: #ff3a10;
    --orange: #ee7325;
    --orange-light: #f08f49;
    --amber: #ffb000;
    --white: #ffffff;
    --ink: #1a0000;
  }
  * { box-sizing: border-box; margin: 0; padding: 0; }
  html, body {
    width: 1200px; height: 912px; overflow: hidden;
    background: var(--stage);
    font-family: "Montserrat", Arial, sans-serif;
  }
  .canvas { position: relative; width: 1200px; height: 912px; }

  .flyer {
    position: absolute; top: 130px; width: 420px; height: 594px; overflow: hidden;
  }
  .flyer--front { left: 130px; }
  .flyer--back { left: 644px; background: var(--panel-black); }

  .tire-photo {
    position: absolute; inset: 0;
    background:
      radial-gradient(ellipse at 70% 20%, var(--red-bright) 0%, transparent 55%),
      radial-gradient(ellipse at 20% 80%, var(--red-main) 0%, transparent 60%),
      linear-gradient(160deg, var(--red-main), var(--red-deep) 55%, var(--red-main));
  }

  .headline {
    position: absolute; top: 32px; left: 0; right: 0;
    text-align: center; color: var(--white);
    font-weight: 900; font-style: italic; font-size: 29px; line-height: 0.92;
    letter-spacing: -1px; text-transform: uppercase;
    text-shadow: 3px 3px 0 var(--ink);
  }
  .headline-note {
    position: absolute; top: 133px; left: 0; right: 0;
    text-align: center; color: var(--ink);
    font-weight: 900; font-style: italic; font-size: 15px; letter-spacing: -0.3px;
    text-transform: uppercase; opacity: 0.8;
  }

  .brand {
    position: absolute; left: 0; right: 0; text-align: center;
  }
  .flyer--front .brand { top: 218px; }
  .flyer--back .brand { top: 150px; }
  .brand-dot {
    display: block; width: 22px; height: 22px; margin: 0 auto 10px;
    border-radius: 50%; background: var(--orange);
  }
  .brand-name {
    display: block; color: var(--orange);
    font-weight: 900; font-size: 50px; line-height: 1; letter-spacing: -1px;
  }
  .phone {
    display: block; margin-top: 12px; color: var(--orange-light);
    font-weight: 900; font-style: italic; font-size: 30px; letter-spacing: -0.5px;
  }
  .flyer--front .phone { text-shadow: 2px 2px 0 var(--ink); }

  .tagline {
    position: absolute; top: 466px; left: 0; right: 0;
    text-align: center; font-weight: 900; font-style: italic;
    font-size: 42px; line-height: 0.92; letter-spacing: -1.5px; text-transform: uppercase;
    background: linear-gradient(180deg, var(--amber), var(--orange) 60%, #e04a00);
    -webkit-background-clip: text; background-clip: text; color: transparent;
    filter: drop-shadow(3px 3px 0 var(--ink));
  }

  .place {
    position: absolute; top: 418px; left: 0; right: 0; text-align: center;
    color: var(--orange); font-weight: 900; font-style: italic; font-size: 18px;
    letter-spacing: -0.3px; text-transform: uppercase;
  }
</style>
</head>
<body>
  <main class="canvas">
    <section class="flyer flyer--front">
      <div class="tire-photo" role="img" aria-label="Close-up photo of stacked car tires with visible tread, tinted red"></div>
      <h1 class="headline">Sale and fitting<br>of tires of all<br>brands</h1>
      <p class="headline-note">(Also ordered by you)</p>
      <div class="brand">
        <span class="brand-dot"></span>
        <span class="brand-name">Marvek Tires</span>
        <span class="phone">079/555.12.34</span>
      </div>
      <p class="tagline">Guarding of<br>your tires!</p>
    </section>

    <section class="flyer flyer--back">
      <div class="brand">
        <span class="brand-dot"></span>
        <span class="brand-name">Marvek Tires</span>
        <span class="phone">079/555.12.34</span>
      </div>
      <p class="place">Val-d'Aubrine</p>
    </section>
  </main>
</body>
</html>
```